Wesbite design for Investment Firm

We want a basic (clean) website that follows the form, fonts and colors of our attachments. This is for a financial investment management firm, but we have a boutique (anti-Wall Street) approach. Site should have an Home Page (Logo up top - room for basic copy on bottom, Philosophy Page (room for Quarterly Letter attachment and basic copy, Performance Page (room for Performance Overview and Performance Analysis and basic copy), Team Page, Commentary Page and Contact

Reason: Some designers have asked for an extension. Again, please only use image of Train Station or Train Station Logo in design.

Target Market(s)

Small and mid-size financial advisors from across the country

Industry/Entity Type

Financial

Number of Pages Required

5+ page

Font styles to use
Other font styles liked:
• Palotino Linotype

Colors
3176b5
cfdeed
ffffff

Requirements
Must have
• Please refer to existing site www.qlvor.example. Of note, this is too complex / cluttered. We simply want Blur, Grey and White consistent with attachments. The copy is pretty good, but will be simplified (and no quotes)
Should not have
• No images other than train station logo and / or train station image

```html
<!DOCTYPE html>
<html lang="en">
<head>
<meta charset="utf-8">
<title>Ashcombe Investment Company</title>
<link rel="stylesheet" href="https://fonts.googleapis.com/css2?family=Open+Sans:ital,wght@0,400;0,600;1,400&family=Roboto:wght@400;500;700&display=swap">
<style>
:root{
  --blue:#3176b5;
  --blue-dark:#1f5a93;
  --blue-pale:#cfdeed;
  --navy:#1c2a3a;
  --ink:#2b2f36;
  --grey:#6b7078;
  --grey-light:#eef1f4;
  --line:#d9dee4;
  --white:#ffffff;
}
*{box-sizing:border-box;margin:0;padding:0}
html,body{width:1200px;height:3100px;overflow:hidden;background:var(--white)}
body{font-family:"Open Sans",Arial,sans-serif;color:var(--ink);font-size:14px;line-height:1.6}
h1,h2,h3,h4{font-family:"Roboto",Arial,sans-serif;font-weight:500}
a{color:inherit;text-decoration:none}

/* header */
.masthead{height:110px;display:flex;align-items:center;justify-content:center}
.brand-name{font-family:"Roboto",Arial,sans-serif;font-weight:500;color:var(--blue-dark);font-size:38px;line-height:1;white-space:nowrap}

.main-nav{height:48px;background:linear-gradient(#3a82c2,var(--blue-dark));display:flex;padding:0 60px;justify-content:space-between}
.main-nav a{color:var(--white);font-family:"Roboto",sans-serif;font-size:16px;line-height:48px;padding:0 36px}
.main-nav a.active{background:rgba(255,255,255,.18)}

/* hero */
.hero{position:relative;height:462px;overflow:hidden}
.hero-photo{position:absolute;inset:0;background:linear-gradient(120deg,#c9d3dd 0%,#8d9cad 35%,#5a6b7e 60%,#9aa8b8 100%)}
.hero-copy{position:absolute;top:200px;width:100%;text-align:center;color:var(--white)}
.hero-copy h1{font-size:46px;font-weight:700;letter-spacing:1px;text-shadow:0 2px 6px rgba(0,0,0,.35)}
.hero-copy p{font-size:30px;font-family:"Roboto",sans-serif;text-shadow:0 2px 6px rgba(0,0,0,.35)}
.hero-dots{position:absolute;right:92px;top:340px;display:flex;gap:10px}
.hero-dots span{width:22px;height:22px;border-radius:50%;background:rgba(0,0,0,.4)}
.hero-curve{position:absolute;left:0;bottom:0}

/* intro */
.intro{height:680px;padding:40px 100px 0;text-align:center}
.section-title{font-size:28px;color:var(--ink);text-transform:uppercase;letter-spacing:.5px}
.intro-text{margin:26px auto 0;width:1000px;font-size:14px;color:var(--grey);line-height:1.75}
.pillars{display:flex;justify-content:space-between;margin-top:60px;padding:0 60px}
.pillar{width:260px}
.pillar-icon{width:110px;height:110px;border-radius:50%;background:var(--blue);margin:0 auto;display:flex;align-items:center;justify-content:center}
.pillar h3{font-size:26px;color:var(--ink);margin-top:22px;font-weight:400}
.pillar p{font-size:13px;color:var(--grey);margin-top:10px}
.more{color:var(--blue-dark);font-size:13px;font-weight:600}

/* what we do */
.what{position:relative;height:520px;background:radial-gradient(circle at 30% 40%,#33475d,var(--navy) 70%)}
.what-card{position:absolute;left:142px;top:90px;width:900px;height:340px;background:var(--white);display:flex;box-shadow:0 6px 24px rgba(0,0,0,.35)}
.what-text{width:500px;padding:36px 40px}
.what-text h2{font-size:30px;font-weight:700;text-transform:uppercase}
.what-text p{font-size:14px;color:var(--grey);margin-top:14px;line-height:1.7}
.btn{display:inline-block;margin-top:20px;background:var(--blue);color:var(--white);border-radius:20px;padding:8px 26px;font-size:13px}
.what-photo{flex:1;margin:20px 20px 20px 0;background:linear-gradient(135deg,#f1f4f7,#b9c9d9 55%,#e5e9ee)}

/* commentary */
.commentary{height:540px;padding:80px 88px 0;display:flex;justify-content:space-between}
.col-head{display:flex;justify-content:space-between;align-items:center;border-bottom:2px solid var(--line);padding-bottom:14px}
.col-head h2{font-size:30px;text-transform:uppercase;font-weight:700}
.arrows{display:flex;gap:8px}
.arrows span{width:22px;height:22px;background:var(--grey-light);display:flex;align-items:center;justify-content:center}
.posts{width:680px}
.post-list{display:flex;gap:36px;margin-top:24px}
.post{width:272px}
.post-photo{position:relative;height:196px;background:linear-gradient(135deg,#9ec1e3,#e8eef4 60%,#b7cbe0)}
.post:nth-child(2) .post-photo{background:linear-gradient(135deg,#e6ebf0,#8fa6bd 60%,#d0dae4)}
.post-date{position:absolute;left:20px;top:26px;width:56px;background:var(--white);text-align:center;font-family:"Roboto",sans-serif}
.post-date b{display:block;font-size:24px;line-height:1.3}
.post-date span{display:block;font-size:12px;color:var(--grey)}
.post-date i{display:block;font-style:normal;font-size:12px;background:var(--ink);color:var(--white)}
.post h3{font-size:16px;font-weight:400;margin-top:14px}
.post p{font-size:12px;color:var(--grey);margin-top:6px}
.letter{width:320px}
.letter .col-head h2{font-size:22px}
.letter-doc{margin:24px auto 0;width:230px;height:300px;border:1px solid var(--line);background:linear-gradient(#fafbfc,#eef1f4);box-shadow:0 2px 8px rgba(0,0,0,.12)}

/* reviews */
.reviews{height:380px;background:linear-gradient(135deg,#3a82c2,var(--blue-dark));color:var(--white);text-align:center;padding-top:40px}
.reviews h2{font-size:32px;font-weight:500;text-transform:uppercase}
.quote{margin:30px auto 0;width:840px;font-size:18px;font-style:italic;line-height:1.7}
.quote-row{display:flex;align-items:center;justify-content:center;gap:40px;margin-top:30px}
.arrow-btn{width:40px;height:40px;border-radius:50%;background:rgba(255,255,255,.25);display:flex;align-items:center;justify-content:center}
.avatar{width:96px;height:96px;border-radius:50%;border:4px solid var(--white);background:linear-gradient(#cfd7df,#8a99a8)}
.cite{margin-top:14px;font-size:13px;color:var(--blue-pale)}

/* footer */
.site-footer{height:316px;display:flex;padding:80px 90px 0;gap:40px}
.foot-brand{width:300px;text-align:center;padding-top:22px}
.foot-brand .brand-name{font-size:20px}
.socials{display:flex;gap:10px;justify-content:center;margin-top:22px}
.socials span{width:30px;height:30px;border-radius:50%;background:var(--blue)}
.foot-col h4{font-size:18px;text-transform:uppercase;margin-bottom:14px}
.foot-col li{list-style:none;font-size:14px;color:var(--grey);line-height:2}
.foot-col li::before{content:"\203A";color:var(--blue);margin-right:10px;font-weight:700}
.quick{width:220px}.links{width:160px}.contact{width:220px}
.contact li::before{content:none}
.contact li{display:flex;gap:12px;align-items:flex-start;line-height:1.6;margin-bottom:10px}
.contact svg{flex:none;margin-top:4px}
.copyright{height:44px;background:var(--grey-light);text-align:center;line-height:44px;font-size:13px;color:var(--grey)}
</style>
</head>
<body>

<header class="masthead">
  <div class="brand-name">Ashcombe Investment Company</div>
</header>

<nav class="main-nav">
  <a class="active" href="#">Home</a><a href="#">Philosophy</a><a href="#">Performance</a><a href="#">Team</a><a href="#">Commentary</a><a href="#">Contact</a>
</nav>

<section class="hero">
  <div class="hero-photo" role="img" aria-label="Photo of an advisor working at a laptop with financial charts on the desk"></div>
  <div class="hero-copy">
    <h1>ASHCOMBE INVESTMENT COMPANY</h1>
    <p>Neque porro quisquam est qui dolorem</p>
  </div>
  <div class="hero-dots"><span></span><span></span></div>
  <svg class="hero-curve" width="1200" height="70" viewBox="0 0 1200 70">
    <path d="M0 10 Q600 90 1200 10 L1200 70 L0 70Z" fill="#ffffff"/>
    <path d="M0 10 Q600 90 1200 10" fill="none" stroke="#3176b5" stroke-width="5"/>
  </svg>
</section>

<section class="intro">
  <h2 class="section-title">Ashcombe Investment Company</h2>
  <p class="intro-text">We founded Ashcombe Investment Company in 1996, initially managing wealth from our family and friends in the spirit of patient ownership. The high expectations of our original investors is a key contributor to our value driven investment philosophy. Based in Dallas, TX, we manage assets for both individuals and institutions. Our investment methodology stresses absolute returns vs. relative performance, blending a combination of fundamental analysis, discipline and patience with the goal of preserving and compounding capital.</p>
  <div class="pillars">
    <div class="pillar">
      <div class="pillar-icon"><svg width="54" height="44" viewBox="0 0 54 44" fill="#fff"><circle cx="27" cy="12" r="9"/><path d="M11 44c0-11 7-17 16-17s16 6 16 17z"/><circle cx="9" cy="16" r="6"/><circle cx="45" cy="16" r="6"/><path d="M0 40c0-8 4-12 9-12 2 0 4 .6 5 1.6-3 3-4.5 6.5-4.5 10.4z"/><path d="M54 40c0-8-4-12-9-12-2 0-4 .6-5 1.6 3 3 4.5 6.5 4.5 10.4z"/></svg></div>
      <h3>Porro Quisquam</h3>
      <p>It is a long established fact that a reader will be distracted by the readable</p>
      <a class="more" href="#">Learn More »</a>
    </div>
    <div class="pillar">
      <div class="pillar-icon"><svg width="54" height="40" viewBox="0 0 54 40"><rect x="8" y="2" width="38" height="26" rx="2" fill="none" stroke="#fff" stroke-width="4"/><path d="M0 32h54l-4 6H4z" fill="#fff"/></svg></div>
      <h3>Dolorem Ipsum</h3>
      <p>It is a long established fact that a reader will be distracted by the readable</p>
      <a class="more" href="#">Learn More »</a>
    </div>
    <div class="pillar">
      <div class="pillar-icon"><svg width="50" height="50" viewBox="0 0 50 50" fill="#fff"><circle cx="25" cy="13" r="11"/><circle cx="13" cy="34" r="11"/><circle cx="37" cy="34" r="11"/><circle cx="25" cy="13" r="4" fill="#3176b5"/><circle cx="13" cy="34" r="4" fill="#3176b5"/><circle cx="37" cy="34" r="4" fill="#3176b5"/></svg></div>
      <h3>Neque Porro</h3>
      <p>It is a long established fact that a reader will be distracted by the readable content</p>
      <a class="more" href="#">Learn More »</a>
    </div>
  </div>
</section>

<section class="what">
  <div class="what-card">
    <div class="what-text">
      <h2>What We Do</h2>
      <p>We founded Ashcombe Investment Company in 1996, initially managing wealth from our family and friends. The high expectations of our original investors is a key contributor to our value driven investment philosophy. Based in Dallas, TX, we manage assets for both individuals and institutions.</p>
      <a class="btn" href="#">Read more</a>
    </div>
    <div class="what-photo" role="img" aria-label="Photo of a laptop and printed financial reports on a desk"></div>
  </div>
</section>

<section class="commentary">
  <div class="posts">
    <div class="col-head">
      <h2>Latest Commentary</h2>
      <div class="arrows">
        <span><svg width="8" height="12" viewBox="0 0 8 12"><path d="M7 1 2 6l5 5" stroke="#6b7078" stroke-width="2" fill="none"/></svg></span>
        <span><svg width="8" height="12" viewBox="0 0 8 12"><path d="M1 1l5 5-5 5" stroke="#6b7078" stroke-width="2" fill="none"/></svg></span>
      </div>
    </div>
    <div class="post-list">
      <article class="post">
        <div class="post-photo" role="img" aria-label="Photo of analysts reviewing a chart">
          <div class="post-date"><span>Jun</span><b>02</b><i>2017</i></div>
        </div>
        <h3>Porro quisquam est</h3>
        <p>It is a long established fact that a reader will be distracted by the readable content of a page.</p>
        <a class="more" href="#">Read More »</a>
      </article>
      <article class="post">
        <div class="post-photo" role="img" aria-label="Photo of a desk with a computer in an office">
          <div class="post-date"><span>Jun</span><b>02</b><i>2017</i></div>
        </div>
        <h3>Dolorem ipsum quia</h3>
        <p>It is a long established fact that a reader will be distracted by the readable content of a page.</p>
        <a class="more" href="#">Read More »</a>
      </article>
    </div>
  </div>
  <div class="letter">
    <div class="col-head"><h2>Investment Adviser's Letter</h2></div>
    <div class="letter-doc" role="img" aria-label="Preview of the quarterly investment adviser's letter"></div>
  </div>
</section>

<section class="reviews">
  <h2>Customers Reviews</h2>
  <p class="quote">“ An investment operation is one which, upon thorough analysis, promises safety of principal and an adequate return. Operations not meeting these requirements are speculative. ”</p>
  <div class="quote-row">
    <span class="arrow-btn"><svg width="10" height="16" viewBox="0 0 10 16"><path d="M8 2 2 8l6 6" stroke="#fff" stroke-width="2.5" fill="none"/></svg></span>
    <div class="avatar" role="img" aria-label="Portrait of the quoted investor"></div>
    <span class="arrow-btn"><svg width="10" height="16" viewBox="0 0 10 16"><path d="M2 2l6 6-6 6" stroke="#fff" stroke-width="2.5" fill="none"/></svg></span>
  </div>
  <p class="cite">Harlan Whitby, Patient Capital</p>
</section>

<footer class="site-footer">
  <div class="foot-brand">
    <div class="brand-name">Ashcombe Investment Company</div>
    <div class="socials"><span></span><span></span><span></span></div>
  </div>
  <div class="foot-col quick">
    <h4>Quick Links</h4>
    <ul><li>Performance Overview</li><li>Performance Analysis</li><li>Qualification Statement</li><li>Ashcombe ADV Part 2</li></ul>
  </div>
  <div class="foot-col links">
    <h4>Links</h4>
    <ul><li>Consectetur</li><li>Quisquam</li><li>Neque</li><li>Dolorem</li></ul>
  </div>
  <div class="foot-col contact">
    <h4>Contact Us</h4>
    <ul>
      <li><svg width="14" height="18" viewBox="0 0 14 18"><path d="M7 0a7 7 0 0 0-7 7c0 5 7 11 7 11s7-6 7-11a7 7 0 0 0-7-7z" fill="#3176b5"/><circle cx="7" cy="7" r="2.5" fill="#fff"/></svg><span>1420 Larkmoor Avenue,<br>Suite 610 Dallas, TX 75000</span></li>
      <li><svg width="16" height="16" viewBox="0 0 16 16"><path d="M3 0h3l1.5 4-2 1.5a9 9 0 0 0 5 5L12 8.5l4 1.5v3a3 3 0 0 1-3 3A13 13 0 0 1 0 3a3 3 0 0 1 3-3z" fill="#3176b5"/></svg><span>214-555-0148</span></li>
      <li><svg width="16" height="12" viewBox="0 0 16 12"><rect width="16" height="12" rx="1" fill="#3176b5"/><path d="M1 1l7 6 7-6" stroke="#fff" stroke-width="1.5" fill="none"/></svg><span>hello@qlvor.example</span></li>
    </ul>
  </div>
</footer>
<div class="copyright">Copyright © 2017. All Rights Reserved.</div>

</body>
</html>
```